Tusk Hollow Lodge website (design only)

Tusk Hollow Lodge (http://www.tuskhollowlodge-mw.example) is a private Safari lodge located in Malawi.
We would like a modern, professional website designed that does not subscribe to the cliched view of a Safari in Africa, but still maintain a wildlife/safari atmosphere.

The aim of our website is to entice people & drive them to the booking form.

Here are some examples of websites that we like. Although we would like our site to be a bit more in line with modern web design trends.

http://www.marulaplains.example/
http://www.kovunde.example/
http://www.tembalorecamp.example/

Requirements
Must have
• Here is a list of the pages required. Most of them will follow a standard content layout. I.e. heading, body and images.

If you take a look at the website, you will get an idea of hoe many page types there are +- 5

http://www.tuskhollowlodge-mw.example/index.htm

About Tusk Hollow
Lirundu Country Club
Rooms
Conferences
Cuisine
Facilities
Your Safari
Activities
Rates & Special Offers
Booking form
Latest Developments
How To Get There
Gallery
Contact Us
Blog / Newsfeed

```html
<!DOCTYPE html>
<html lang="en">
<head>
<meta charset="utf-8">
<title>Tusk Hollow Lodge</title>
<link href="https://fonts.googleapis.com/css2?family=Roboto+Condensed:wght@400;500;700&family=Tinos:ital@0;1&family=Arimo:wght@400;700&family=Open+Sans:wght@400&display=swap" rel="stylesheet">
<style>
:root{
  --red:#a30d08;
  --red-deep:#8e0c07;
  --red-tab:#b8160f;
  --icon:#6a0c07;
  --brown:#6d4e35;
  --tan:#a6845c;
  --panel:#241a12;
  --lime:#d6d62a;
  --blue:#1a47d8;
  --ink:#111;
  --maroon:#8a0f0a;
  --white:#fff;
}
*{margin:0;padding:0;box-sizing:border-box}
html,body{width:1161px;height:1200px;overflow:hidden;background:var(--white)}
.page{position:relative;width:1161px;height:1200px;font-family:"Tinos",serif;color:var(--ink)}
.brand{position:absolute;left:0;top:0;width:250px;height:167px}
.brand-mark{position:absolute;left:114px;top:60px;width:22px;height:22px;border-radius:50%;background:var(--red-deep)}
.brand-name{position:absolute;left:0;top:119px;width:250px;text-align:center;font-family:"Tinos",serif;font-size:18px;letter-spacing:.5px;color:#222;text-transform:uppercase;white-space:nowrap}
.phones{position:absolute;right:33px;top:48px;text-align:right;font-family:"Tinos",serif;font-size:20.5px;line-height:24px;color:var(--blue)}
.main-nav{position:absolute;left:250px;top:109px;width:901px;height:58px;background:var(--red)}
.main-nav a{position:absolute;top:22px;font-family:"Roboto Condensed",sans-serif;font-weight:400;font-size:12.8px;color:var(--white);text-decoration:none;text-transform:uppercase;white-space:nowrap}
.main-nav .current{top:-6px;left:17px;width:92px;height:64px;background:var(--red-tab);border-radius:10px 10px 0 0;display:flex;align-items:center;justify-content:center;padding-top:4px;font-size:15px}
.side-nav{position:absolute;left:0;top:169px;width:250px;height:299px;background:var(--brown);border-bottom:1px solid var(--white)}
.side-nav a{display:block;height:34.5px;line-height:34.5px;padding-left:23px;font-family:"Roboto Condensed",sans-serif;font-weight:400;font-size:12.6px;color:var(--white);text-decoration:none;text-transform:uppercase}
.side-nav a:nth-child(odd){background:var(--brown)}
.side-nav a:nth-child(even){background:var(--tan)}
.hero{position:absolute;left:250px;top:167px;width:901px;height:302px;background:linear-gradient(180deg,#cdb596 0%,#b89873 45%,#c9a46c 80%,#e3c38a 100%)}
.hero-caption{position:absolute;left:10px;bottom:22px;font-family:"Open Sans",sans-serif;font-size:19px;line-height:23px;color:#000}
.hero-caption small{font-size:15px}
.events{position:absolute;left:0;top:469px;width:250px;height:371px;background:var(--panel);color:var(--white)}
.events-head{position:absolute;left:9px;top:14px;display:flex;align-items:center;gap:10px;font-family:"Roboto Condensed",sans-serif;font-size:16px;text-transform:uppercase}
.events-title{position:absolute;left:15px;top:74px;font-family:"Arimo",sans-serif;font-weight:400;font-size:14px;color:var(--lime);text-transform:uppercase}
.events-text{position:absolute;left:15px;top:106px;width:228px;font-family:"Arimo",sans-serif;font-size:11.8px;letter-spacing:-.35px;line-height:16.4px}
.read-more{position:absolute;left:16px;top:318px;width:167px;height:27px;border-radius:14px;background:var(--lime);font-family:"Roboto Condensed",sans-serif;font-weight:700;font-size:12px;color:#222;text-transform:uppercase;line-height:27px;padding-left:28px;text-decoration:none}
.intro{position:absolute;left:272px;top:505px;width:855px;font-style:italic;font-size:16px;line-height:20.6px}
.intro p{margin-bottom:20.6px}
.intro .phase{color:var(--maroon)}
.amenities{position:absolute;left:0;top:840px;width:1151px;height:228px;background:linear-gradient(180deg,var(--red-deep),var(--red));border-radius:5px}
.amenity{position:absolute;top:42px;width:170px;margin-left:-85px;text-align:center;color:var(--white);font-size:16.5px}
.amenity svg{display:block;margin:0 auto 14px;height:120px}
.credit{position:absolute;right:24px;top:1088px;font-size:12px}
</style>
</head>
<body>
<div class="page">
  <header>
    <div class="brand"><span class="brand-mark"></span><span class="brand-name">Tusk Hollow Lodge</span></div>
    <div class="phones">Tel : +265 (0) 555 014 620<br>: +265 (0) 555 014 621</div>
    <nav class="main-nav">
      <a class="current" href="#">Welcome</a>
      <a href="#" style="left:117px">About Tusk Hollow</a>
      <a href="#" style="left:245px">Latest Developments</a>
      <a href="#" style="left:390px">How to get there</a>
      <a href="#" style="left:513px">Gallery</a>
      <a href="#" style="left:580px">Contact Us</a>
      <a href="#" style="left:669px">Our Blog</a>
      <a href="#" style="left:745px">Booking Requests</a>
    </nav>
  </header>

  <nav class="side-nav">
    <a href="#">Rooms</a><a href="#">Conferences</a><a href="#">Cuisine</a><a href="#">Facilities</a>
    <a href="#">Your Safari</a><a href="#">Activities</a><a href="#">Rates &amp; Special Offers</a><a href="#">Booking Requests</a>
  </nav>

  <section class="hero" role="img" aria-label="Three elephants walking through golden savanna grass">
    <p class="hero-caption"><small>Warmest welcome to the unique </small>Malawi experience. lodge complex, game park, the 18 hole<br>Lirundu golf club and Lusewe dam.</p>
  </section>

  <aside class="events">
    <div class="events-head">
      <svg width="46" height="40" viewBox="0 0 46 40" aria-hidden="true"><rect x="2" y="5" width="42" height="33" rx="5" fill="none" stroke="#fff" stroke-width="3"/><rect x="2" y="5" width="42" height="9" fill="#fff"/><rect x="11" y="1" width="4" height="8" fill="#fff"/><rect x="31" y="1" width="4" height="8" fill="#fff"/><text x="23" y="34" text-anchor="middle" font-family="Arimo,sans-serif" font-weight="700" font-size="19" fill="#fff">5</text></svg>
      <span>Calendar Events</span>
    </div>
    <h3 class="events-title">Safari</h3>
    <p class="events-text">We have supplemented our game park with indigenous Malawi wild life which consists of&nbsp; sable, waterbuck, zebra, impala, wildebeest, nyala, giraffe and numerous duiker and smaller wild cats and otters. we have recently introduced from Zambia new breeding stock of roan, kudu and eland and thus now have, in the sanctuary, the “big five” of the antelope family. Bird life is prolific as are the wild flowers and shrubs including massive Mbawa trees and Chiwali palms.</p>
    <a class="read-more" href="#">Read More</a>
  </aside>

  <main class="intro">
    <p>A multi million&nbsp; dollar development at Kaluzi estate, Nthandi on Mlenje road a short drive from Malawi's southern towns creating a fascinating paradise&nbsp; for multiple leisure activities and conserving Malawi wildlife.Our Lodge also has beautifully designed and built&nbsp; in golden colored rock.</p>
    <p class="phase">The 1st phase was completed in 2007, and is approx 1800 sq. meters, comprising of:<br>A fully carpeted and elegantly furnished restaurant&nbsp; with seating for up to 80 guests and exceptional cuisine to completely satisfy most palates.<br>A stately carpeted conference hall for up to 45 people, 5 luxurious and spacious ensuite cottages with lounge and private verandah accessing a beautiful 18 meter swimming pool with cascading waterfall.</p>
    <p>The entire Kaluzi estate comprises of 220 hectares of exquisite, undulating indigenous forest and grassland and is protected by an 8 km perimeter road enclosed by a 3 meter high game fence on either side of the road .<br>There are at least 40 kms of dirt roads and numerous paths for drives and walks, the most beautiful of which is along the Kaluzi stream which dissects the property.</p>
  </main>

  <section class="amenities">
    <div class="amenity" style="left:88px"><svg viewBox="0 0 100 120" width="98"><path d="M5 60 Q50 -6 95 60 Q84 52 72 60 Q61 52 50 60 Q39 52 28 60 Q16 52 5 60Z" fill="var(--icon)"/><circle cx="50" cy="12" r="3" fill="var(--icon)"/><path d="M50 58 V102 Q50 112 41 112 Q33 112 33 104" fill="none" stroke="var(--icon)" stroke-width="6" stroke-linecap="round"/></svg>restaurant facilities</div>
    <div class="amenity" style="left:296px"><svg viewBox="0 0 120 120" width="120"><path d="M6 52 A75 75 0 0 1 114 52" fill="none" stroke="var(--icon)" stroke-width="13"/><path d="M28 74 A45 45 0 0 1 92 74" fill="none" stroke="var(--icon)" stroke-width="13"/><circle cx="60" cy="100" r="9" fill="var(--icon)"/></svg>wifi connections</div>
    <div class="amenity" style="left:488px"><svg viewBox="0 0 120 120" width="120"><circle cx="100" cy="62" r="13" fill="var(--icon)"/><path d="M8 86 L44 58 L38 46 L82 36 L90 48 L60 54 L76 80Z" fill="var(--icon)"/><path d="M2 98 q10-8 20 0 t20 0 t20 0 t20 0 t20 0 t20 0" fill="none" stroke="var(--icon)" stroke-width="7"/></svg>swimming pool</div>
    <div class="amenity" style="left:649px"><svg viewBox="0 0 60 120" width="60"><path d="M4 2 V40 Q4 50 14 52 V118 H22 V52 Q32 50 32 40 V2 H27 V36 H22 V2 H14 V36 H9 V2Z" fill="var(--icon)"/><path d="M40 2 Q56 6 56 44 V118 H44 V66 H40Z" fill="var(--icon)"/></svg>cuisine</div>
    <div class="amenity" style="left:795px"><svg viewBox="0 0 60 120" width="60"><circle cx="30" cy="10" r="10" fill="var(--icon)"/><path d="M18 24 H42 L56 70 H48 L52 80 H40 V118 H32 V80 H28 V118 H20 V80 H8 L12 70 H4Z" fill="var(--icon)"/></svg>room service</div>
    <div class="amenity" style="left:935px"><svg viewBox="0 0 80 120" width="80"><path d="M4 8 H44 Q76 8 76 42 Q76 76 44 76 H28 V116 H4Z M28 30 V54 H42 Q52 54 52 42 Q52 30 42 30Z" fill="var(--icon)" fill-rule="evenodd"/></svg>parking facilities</div>
  </section>

  <footer class="credit">2012 © www.tuskhollowlodge-mw.example | All rights reserved</footer>
</div>
</body>
</html>
```